High Tech Real Estate Startup needs a business card

We are developing an innovative real estate marketing product based around advanced search and virtual reality.

We talk to people, we need business cards.

Target Market(s)

The target market is technology professionals and realtors.

Contact Information for Business Card

The information to be included will include

Name
Title
Phone Number
E-mail Address
www.zelquin.com

It should use simple iconography for each one of those fields.

Font styles to use
Other font styles liked:
• Co, Jubilat, Avenir

Colors

Designer to choose colors to be used in the design.

Requirements
Must have
• Clean aesthetic,
• Good use of negative space.
• It should use our company logo, shown in the attached file. It is able to use the negative of that logo (coloured font and white background) and I have attached other acceptable accent colours in a swatch file.
Should not have
• Should not be too busy
• No extraneous text (slogans, tag lines etc)

```html
<!DOCTYPE html>
<html lang="en">
<head>
<meta charset="utf-8">
<title>Zelquin Business Card</title>
<link rel="stylesheet" href="https://fonts.googleapis.com/css2?family=Work+Sans:wght@300;400;500;600&display=swap">
<style>
  :root {
    --backdrop: #2b2624;
    --card: #17181a;
    --card-edge: #222326;
    --silver: #c9c9c9;
    --silver-soft: #a9a9a9;
    --rule: #8a8a8a;
  }
  * { margin: 0; padding: 0; box-sizing: border-box; }
  html, body {
    width: 1200px; height: 715px; overflow: hidden;
    background: var(--backdrop);
    font-family: "Work Sans", sans-serif;
  }
  .stage {
    width: 1200px; height: 715px;
    display: flex; align-items: center; justify-content: center; gap: 40px;
  }
  .card {
    width: 540px; height: 309px;
    background: var(--card);
    border: 1px solid var(--card-edge);
    border-radius: 6px;
    position: relative;
    box-shadow: 0 18px 40px rgba(0,0,0,.45);
  }
  .brand {
    display: flex; align-items: center; gap: 14px;
    color: var(--silver);
    font-weight: 500; letter-spacing: 3px;
  }
  .brand-mark {
    display: block; background: var(--silver);
  }
  .card-front .brand {
    position: absolute; left: 50%; top: 50%;
    transform: translate(-50%, -50%);
    font-size: 30px;
  }
  .card-front .brand-mark { width: 34px; height: 34px; }
  .card-back .brand {
    position: absolute; left: 40px; top: 50%;
    transform: translateY(-50%);
    font-size: 22px;
  }
  .card-back .brand-mark { width: 24px; height: 24px; }
  .divider {
    position: absolute; left: 262px; top: 74px;
    width: 1px; height: 160px; background: var(--rule);
  }
  .contact {
    position: absolute; left: 290px; top: 72px;
    color: var(--silver-soft);
    font-size: 13px; line-height: 1.45; font-weight: 400;
  }
  .contact-name {
    color: var(--silver); font-size: 19px; font-weight: 600;
    letter-spacing: 1px; text-transform: uppercase; line-height: 1.2;
  }
  .contact-title { font-weight: 300; margin-bottom: 10px; }
  .contact-address { margin-bottom: 2px; }
  .contact-line { display: flex; align-items: center; gap: 8px; }
  .contact-line svg { width: 11px; height: 11px; fill: none; stroke: var(--silver-soft); stroke-width: 1.6; flex: none; }
</style>
</head>
<body>
<main class="stage">
  <section class="card card-front" aria-label="Card front">
    <div class="brand"><span class="brand-mark"></span>ZELQUIN</div>
  </section>

  <section class="card card-back" aria-label="Card back">
    <div class="brand"><span class="brand-mark"></span>ZELQUIN</div>
    <div class="divider"></div>
    <div class="contact">
      <p class="contact-name">Dorian Vale</p>
      <p class="contact-title">Director</p>
      <p class="contact-address">417 Larkspur Bend Rd.<br>Fernwick, OR 97402</p>
      <p class="contact-line">
        <svg viewBox="0 0 12 12" aria-hidden="true"><path d="M2.5 1.5l2 .5.6 2.3-1.2 1a6 6 0 0 0 2.8 2.8l1-1.2 2.3.6.5 2-1.3 1A8.5 8.5 0 0 1 1.5 2.8z"/></svg>
        +1-555-210-7391
      </p>
      <p class="contact-line">
        <svg viewBox="0 0 12 12" aria-hidden="true"><rect x="1" y="2.5" width="10" height="7"/><path d="M1 2.5l5 4 5-4"/></svg>
        info@zelquin.com
      </p>
      <p class="contact-line">
        <svg viewBox="0 0 12 12" aria-hidden="true"><circle cx="6" cy="6" r="4.8"/><path d="M1.2 6h9.6M6 1.2c-2.4 2.6-2.4 7 0 9.6M6 1.2c2.4 2.6 2.4 7 0 9.6"/></svg>
        www.zelquin.com
      </p>
    </div>
  </section>
</main>
</body>
</html>
```